Estate Planning Law Firm opening new branch in Florida

I am an experienced estate planning attorney that recently relocated to Florida. Looking for a banner Ad to place on platforms such as HomeLane, Chatterbox and Picturely to create publicity for firm and new leads.

```html
<!DOCTYPE html>
<html lang="en">
<head>
<meta charset="UTF-8">
<title>Calmwater Law Firm – Estate &amp; Financial Planning</title>
<link href="https://fonts.googleapis.com/css2?family=Cinzel:wght@500&family=Libre+Baskerville:wght@700&family=Lato:wght@700;900&display=swap" rel="stylesheet">
<style>
  :root {
    --navy: #1f3a4d;
    --brand-teal: #1e6f6c;
    --sky-top: #ffffff;
    --sky-mid: #cde4f0;
    --sky-low: #8fc0d8;
    --city-light: #6f8fa2;
    --city: #4a6172;
    --city-dark: #37505c;
    --water: #3b6d70;
    --teal: #1d6b69;
    --teal-deep: #135a5a;
    --white: #ffffff;
  }
  html, body {
    margin: 0;
    padding: 0;
    width: 1200px;
    height: 1200px;
    overflow: hidden;
    background: var(--white);
  }
  .ad {
    position: relative;
    width: 1200px;
    height: 1200px;
    overflow: hidden;
    font-family: "Lato", sans-serif;
    background: linear-gradient(180deg,
      var(--sky-top) 0%,
      var(--sky-mid) 12%,
      var(--sky-low) 30%,
      var(--sky-low) 40%,
      var(--water) 62%,
      var(--teal) 75%,
      var(--teal-deep) 100%);
  }
  .skyline-photo {
    position: absolute;
    left: 0;
    top: 160px;
    width: 1200px;
    height: 620px;
    background:
      linear-gradient(180deg, rgba(143,192,216,0) 0%, rgba(143,192,216,0) 55%, rgba(212,140,70,0.55) 64%, rgba(59,109,112,0.0) 72%),
      linear-gradient(180deg,
        var(--sky-low) 0%,
        var(--city-light) 22%,
        var(--city) 45%,
        var(--city-dark) 62%,
        var(--water) 78%,
        rgba(29,107,105,0) 100%);
    -webkit-mask-image: linear-gradient(180deg, transparent 0%, #000 14%, #000 82%, transparent 100%);
    mask-image: linear-gradient(180deg, transparent 0%, #000 14%, #000 82%, transparent 100%);
  }
  .diagonal-bands {
    position: absolute;
    inset: 0;
    width: 1200px;
    height: 1200px;
  }
  .brand {
    position: absolute;
    top: 58px;
    left: 0;
    right: 0;
    display: flex;
    justify-content: center;
    align-items: flex-start;
    gap: 26px;
    color: var(--navy);
    font-family: "Cinzel", serif;
    font-weight: 500;
  }
  .brand-mark {
    width: 82px;
    height: 82px;
    margin-top: 4px;
    background: var(--brand-teal);
  }
  .brand-text {
    text-align: center;
  }
  .brand-name {
    font-size: 86px;
    line-height: 1;
    letter-spacing: 2px;
  }
  .brand-suffix {
    display: flex;
    align-items: center;
    justify-content: center;
    gap: 14px;
    margin-top: 12px;
    font-size: 27px;
    letter-spacing: 1px;
  }
  .brand-suffix .rule {
    width: 100px;
    height: 2px;
    background: var(--brand-teal);
  }
  .headline {
    position: absolute;
    top: 748px;
    left: 0;
    right: 0;
    margin: 0;
    text-align: center;
    color: var(--white);
    font-family: "Libre Baskerville", serif;
    font-weight: 700;
    font-size: 50px;
    line-height: 100px;
    letter-spacing: 0.5px;
    text-shadow: 3px 4px 6px rgba(0,0,0,0.5);
  }
  .location {
    position: absolute;
    top: 993px;
    left: 0;
    right: 0;
    margin: 0;
    text-align: center;
    color: var(--white);
    font-weight: 900;
    font-size: 24px;
    letter-spacing: 0.3px;
  }
  .phone {
    position: absolute;
    top: 1082px;
    left: 0;
    right: 0;
    display: flex;
    align-items: center;
    justify-content: center;
    gap: 22px;
    color: var(--white);
    font-weight: 700;
    font-size: 54px;
  }
  .phone-icon {
    width: 58px;
    height: 58px;
  }
</style>
</head>
<body>
  <div class="ad">
    <div class="skyline-photo" role="img" aria-label="Photograph of a Florida city skyline at dusk with a lit bridge over a calm river"></div>

    <svg class="diagonal-bands" viewBox="0 0 1200 1200" aria-hidden="true">
      <polygon points="0,830 560,660 1200,660 1200,700 0,1060" fill="#ffffff" opacity="0.05"/>
      <polygon points="0,1100 900,780 1200,780 1200,820 0,1200" fill="#000000" opacity="0.05"/>
    </svg>

    <header class="brand">
      <span class="brand-mark" aria-hidden="true"></span>
      <div class="brand-text">
        <div class="brand-name">CALMWATER</div>
        <div class="brand-suffix"><span class="rule"></span>LAW FIRM, PLLC<span class="rule"></span></div>
      </div>
    </header>

    <h1 class="headline">ESTATE PLANNING &amp; FINANCIAL<br>PLANNING UNDER ONE ROOF</h1>

    <p class="location">MELBOURNE, FL ESTATE AND FINANCIAL PLANNING</p>

    <div class="phone">
      <svg class="phone-icon" viewBox="0 0 58 58" aria-hidden="true">
        <rect x="0" y="0" width="58" height="58" rx="10" fill="#ffffff"/>
        <path d="M19 13c1.5-1 3.5-.6 4.4 1l3 5.2c.8 1.4.4 3.1-.8 4.1l-2.2 1.7c1.8 4 5 7.3 9 9.2l1.8-2.2c1-1.2 2.8-1.6 4.2-.8l5.2 3c1.6.9 2 2.9 1 4.4l-1.6 2.3c-1.4 2-4 2.8-6.3 2C23.6 39.6 17.6 33.4 14.4 25.3c-.9-2.3 0-4.9 2-6.3z" fill="#1d6b69"/>
      </svg>
      <span class="phone-number">(321) 555-0148</span>
    </div>
  </div>
</body>
</html>
```